Brimsett Gardening Fresh New Website

We are looking to create a simple fresh website for our landscaping business. The website should appeal to a 'high end' audience. We deal with a lot of Embassies and affluent clients who have extremely large gardens that are meticulously maintained. The site is about communicating our excellent landscaping and customer service skills and encouraging new clients to reach out and engage us to take care of their gardens.

The website is basically going to be our business card, it will have almost no functionality other than two 'contact us' forms, one for smaller clients and one for more detailed projects.

The website will not have a lot of written content and will have to show photos of beautifully landscaped gardens.

The main logo in black will influence the site, however, we are open to all suggestions.

We are expecting to have the following pages:
Home Page
Services
About Us
Contact Us
Showcase (photo gallery of our work)

We need someone who can code it to wordpress and be available for minor changes over a number of days. They will be simple tweaks.

```html
<!DOCTYPE html>
<html lang="en">
<head>
<meta charset="utf-8">
<title>Brimsett Gardening</title>
<link href="https://fonts.googleapis.com/css2?family=Libre+Baskerville:wght@400;700&family=Poppins:ital,wght@0,400;0,500;0,600;0,700;1,600&display=swap" rel="stylesheet">
<style>
:root{
  --ink:#111111;
  --gold:#c9962f;
  --gold-light:#f3d24a;
  --brown:#a36f22;
  --peach:#fdf0dc;
  --white:#ffffff;
  --text:#2a2a2a;
  --line:#d9d4cb;
}
*{box-sizing:border-box;margin:0;padding:0}
html,body{width:1200px;height:4274px;overflow:hidden}
body{position:relative;background:var(--white);font-family:'Poppins',sans-serif;color:var(--text)}
.abs{position:absolute}
.serif{font-family:'Libre Baskerville',serif}

/* header */
.site-header{left:0;top:0;width:1200px;height:91px;background:var(--ink);color:var(--white)}
.social{left:142px;top:16px;display:flex;gap:10px}
.social span{width:14px;height:14px;border-radius:50%;border:1.5px solid #bbb;display:block}
.header-rule{top:44px;height:1px;background:#3a3a3a}
.nav-link{top:58px;font-size:12px;font-weight:500;color:var(--white)}
.brand-name{font-family:'Poppins',sans-serif;font-weight:600;color:var(--white);text-align:center}
.brand{left:500px;top:30px;width:200px;font-size:15px;line-height:1.3}
.phone{left:958px;top:16px;font-size:12px;display:flex;align-items:center;gap:8px}

/* hero */
.hero{left:0;top:91px;width:1200px;height:565px;background:linear-gradient(180deg,#6d7a74 0%,#5c6658 35%,#3f5a2c 70%,#6a3a2a 88%,#2d3a1d 100%)}
.hero-kicker{left:0;top:290px;width:1200px;text-align:center;color:var(--white);font-size:23px;letter-spacing:4px;font-weight:500}
.hero-title{left:0;top:328px;width:1200px;text-align:center;color:var(--white);font-size:48px;line-height:57px;font-weight:700}
.btn-gold{background:linear-gradient(90deg,#b88a1f,var(--gold-light));color:var(--ink);font-size:12px;font-weight:600;display:flex;align-items:center;justify-content:center}

/* quote form */
.quote{left:694px;top:609px;width:370px;height:442px;background:var(--ink);border:5px solid var(--gold)}
.quote h3{position:absolute;left:23px;top:25px;font-size:21px;line-height:27px;color:var(--white);font-weight:400}
.quote h3 em{color:var(--gold);font-style:normal}
.qfield{position:absolute;left:23px;width:315px;height:34px;border:1px solid #cfcfcf;color:var(--white);font-size:11.5px;padding:9px 14px}
.qfield i{color:#e04848;font-style:normal}

/* about */
.about-title{left:141px;top:708px;font-size:35px;line-height:46px;font-weight:700;color:var(--ink)}
.about-title span{color:var(--gold)}
.about-copy{left:141px;top:808px;width:450px;font-size:11.5px;line-height:22.5px;color:var(--ink)}
.about-copy p+p{margin-top:6px}

/* services */
.services{left:0;top:1147px;width:1200px;height:573px;background:linear-gradient(180deg,#f2e6cf,#efe2c6 60%,#e8dcc2)}
.section-title{left:0;width:1200px;text-align:center;font-size:34px;font-weight:600;color:var(--ink)}
.section-title span{color:var(--brown)}
.svc-card{top:1300px;width:219px;height:257px;border-radius:10px;overflow:hidden}
.svc-card .shade{position:absolute;inset:0}
.svc-card .body{position:absolute;left:0;right:0;top:138px;text-align:center;color:var(--white)}
.svc-card h4{font-size:16px;font-weight:600}
.svc-card p{font-size:11.5px;line-height:18px;margin-top:4px;padding:0 22px}
.svc-card a{display:inline-block;margin-top:5px;font-size:11px;font-weight:600;color:var(--white);text-decoration:underline}
.btn-brown{background:var(--brown);color:var(--white);font-size:12px;font-weight:600;border-radius:20px;display:flex;align-items:center;justify-content:center;letter-spacing:.3px}

/* gallery */
.g-tile{width:292px;height:292px;border-radius:14px}
.g-brand{display:flex;align-items:center;justify-content:center;font-size:22px;line-height:1.3}

/* testimonials */
.testimonials{left:0;top:2691px;width:1200px;height:530px;background:var(--peach)}
.t-card{top:2859px;width:292px;height:282px;background:var(--white);border-radius:26px;box-shadow:0 6px 18px rgba(0,0,0,.06)}
.stars{position:absolute;left:28px;top:30px;display:flex;gap:7px}
.g-dot{position:absolute;right:28px;top:26px;width:24px;height:24px;border-radius:50%;border:3px solid #8a8a8a}
.t-card p{position:absolute;left:28px;top:72px;width:242px;font-size:12.3px;line-height:21.5px;color:var(--ink)}
.t-card h5{position:absolute;left:28px;top:229px;font-size:15px;font-weight:600;font-style:italic;color:var(--ink)}
.arrow{width:54px;height:54px;border-radius:50%;display:flex;align-items:center;justify-content:center}

/* contact */
.contact{left:141px;top:3307px;width:918px;height:430px;background:var(--white);border-radius:26px;box-shadow:0 4px 24px rgba(0,0,0,.07)}
.contact-panel{left:141px;top:3307px;width:335px;height:430px;border-radius:26px;background:linear-gradient(160deg,#2a2720,#14130f 55%,#1d1a14)}
.cp-kicker{left:177px;top:3367px;font-size:12px;font-weight:600;color:var(--gold);letter-spacing:.5px}
.cp-title{left:177px;top:3394px;font-size:25px;line-height:38px;color:var(--white);font-weight:400}
.cp-item{left:177px;display:flex;gap:13px;align-items:flex-start;color:var(--white);font-size:12.5px;line-height:21px}
.cp-icon{width:28px;height:28px;border-radius:50%;border:1.5px solid var(--white);display:flex;align-items:center;justify-content:center;flex:none}
.form-title{left:515px;top:3342px;font-size:15px;font-weight:600;color:var(--ink);letter-spacing:.4px}
.cfield{height:34px;border:1px solid var(--line);font-size:11px;color:#666;padding:9px 16px}
.cfield.active{border-color:var(--gold);color:var(--ink)}

/* footer */
.footer{left:0;top:3828px;width:1200px;height:446px;background:linear-gradient(180deg,#24221b,#16150f)}
.f-brand{left:450px;top:3930px;width:300px;font-size:24px;line-height:1.3}
.f-link{top:4060px;font-size:14px;color:var(--white)}
.f-rule{left:141px;width:918px;height:1px;background:#7d7868}
.f-info{top:4145px;display:flex;gap:12px;align-items:center;color:var(--white);font-size:12.5px;line-height:20px}
.copyright{left:0;top:4229px;width:1200px;text-align:center;color:var(--white);font-size:12.5px}
</style>
</head>
<body>

<!-- header -->
<header class="abs site-header">
  <div class="abs social" aria-label="Social links"><span></span><span></span><span></span></div>
  <div class="abs header-rule" style="left:141px;width:283px"></div>
  <div class="abs header-rule" style="left:792px;width:267px"></div>
  <a class="abs nav-link" style="left:141px">Home</a>
  <a class="abs nav-link" style="left:246px">Services</a>
  <a class="abs nav-link" style="left:366px">Gallery</a>
  <div class="abs brand brand-name">Brimsett Gardening</div>
  <a class="abs nav-link" style="left:714px">About Us</a>
  <a class="abs nav-link" style="left:838px">Contact Us</a>
  <a class="abs nav-link" style="left:971px;display:flex;align-items:center;gap:6px">Projects For
    <svg width="12" height="8" viewBox="0 0 12 8"><path d="M1 1l5 5 5-5" fill="none" stroke="#fff" stroke-width="1.8"/></svg></a>
  <div class="abs phone">
    <svg width="14" height="14" viewBox="0 0 24 24"><path d="M5 3h4l2 5-2.5 1.5a11 11 0 0 0 6 6L16 13l5 2v4a2 2 0 0 1-2 2A17 17 0 0 1 3 5a2 2 0 0 1 2-2z" fill="none" stroke="#fff" stroke-width="1.8"/></svg>
    123 456 7890
  </div>
</header>

<!-- hero -->
<section class="abs hero" role="img" aria-label="Photo of a grey shingled house with a manicured lawn, trees and red flower beds"></section>
<div class="abs hero-kicker">LANDSCAPE PROS</div>
<h1 class="abs hero-title serif">Stunning Landscapes To<br>Inspire Your Family</h1>
<a class="abs btn-gold" style="left:534px;top:453px;width:132px;height:34px">Request A Quote</a>

<!-- quote form -->
<form class="abs quote">
  <h3 class="serif"><em>24% Off</em> For New<br>Landscape Services</h3>
  <div class="qfield" style="top:94px">Name<i>*</i></div>
  <div class="qfield" style="top:136px">Email<i>*</i></div>
  <div class="qfield" style="top:178px">Phone Number<i>*</i></div>
  <div class="qfield" style="top:220px">Street Address &amp; Zip Code<i>*</i></div>
  <div class="qfield" style="top:262px;display:flex;justify-content:space-between;align-items:center;padding-top:0;padding-bottom:0">Which Service Would You Like A Bill For?
    <svg width="12" height="8" viewBox="0 0 12 8"><path d="M1 1l5 5 5-5" fill="none" stroke="#fff" stroke-width="1.8"/></svg></div>
  <div class="qfield" style="top:304px;height:70px">Message</div>
  <div class="abs btn-gold" style="left:23px;top:380px;width:315px;height:34px">Request A Quote</div>
</form>

<!-- about -->
<h2 class="abs about-title serif">About<br><span>Brimsett Gardening</span></h2>
<div class="abs about-copy">
  <p>Lorem Ipsum Is Simply Dummy Text Of The Printing And Typesetting Industry. Lorem Ipsum Has Been The Industry's Standard Dummy Text Ever Since The 1500s, When An Unknown Printer Took A Galley Of Type And Scrambled It To Make A Type Specimen Book.</p>
  <p>Lorem Ipsum Is Simply Dummy Text Of The Printing And Typesetting Industry. Lorem Ipsum Has Been The Industry's Standard Dummy Text Ever Since The 1500s, When&nbsp; And Scrambled It To Make A Type Specimen Book.</p>
</div>
<a class="abs btn-gold" style="left:141px;top:989px;width:94px;height:34px">Read More</a>

<!-- services -->
<section class="abs services" role="img" aria-label="Faded background photo of a park with trees"></section>
<h2 class="abs section-title" style="top:1212px">Our <span>Services</span></h2>

<div class="abs svc-card" style="left:141px">
  <div class="shade" role="img" aria-label="Photo of a single tree on a lawn" style="background:linear-gradient(180deg,#3c5a3a,#2b4229 55%,#1e2a1a)"></div>
  <div class="body"><h4>Landscaping</h4><p>Lorem ipsum dolor sit amet, consectetur adipiscing.</p><a>Read More</a></div>
</div>
<div class="abs svc-card" style="left:374px">
  <div class="shade" role="img" aria-label="Photo of lawn care on a garden" style="background:linear-gradient(180deg,#b07a42,#8d6a3a 50%,#5f5a2a)"></div>
  <div class="body"><h4>Lawn Service</h4><p>Lorem ipsum dolor sit amet, consectetur adipiscing.</p><a>Read More</a></div>
</div>
<div class="abs svc-card" style="left:607px">
  <div class="shade" role="img" aria-label="Photo of a wheelbarrow full of grass cuttings" style="background:linear-gradient(180deg,#3d4a33,#4a5a3e 50%,#2c3325)"></div>
  <div class="body"><h4>Lawn Maintenance</h4><p>Lorem ipsum dolor sit amet, consectetur adipiscing.</p><a>Read More</a></div>
</div>
<div class="abs svc-card" style="left:840px">
  <div class="shade" role="img" aria-label="Photo of a tree care worker in safety gear" style="background:linear-gradient(180deg,#5a4a3c,#4a4034 50%,#2e2a22)"></div>
  <div class="body"><h4>Tree Services</h4><p>Lorem ipsum dolor sit amet, consectetur adipiscing.</p><a>Read More</a></div>
</div>
<a class="abs btn-brown" style="left:518px;top:1607px;width:164px;height:37px">VIEW ALL SERVICES</a>

<!-- gallery -->
<h2 class="abs section-title" style="top:1807px">Our <span>Gallery</span></h2>
<div class="abs g-tile" style="left:141px;top:1907px;background:linear-gradient(160deg,#6a9a3a,#3f6a2c 50%,#5a7a6a)" role="img" aria-label="Photo of a wooden boardwalk through green gardens"></div>
<div class="abs g-tile" style="left:453px;top:1907px;background:linear-gradient(180deg,#7a9a4a,#4a6a2a 50%,#8a8a80)" role="img" aria-label="Photo of a path beneath green garden arches"></div>
<div class="abs g-tile" style="left:764px;top:1907px;background:linear-gradient(180deg,#2f8fd8,#7ab8e8 40%,#c9443a 58%,#5aa82a 75%,#6ab82e)" role="img" aria-label="Photo of red flower beds on a bright lawn under blue sky"></div>
<div class="abs g-tile" style="left:141px;top:2219px;background:linear-gradient(180deg,#c89a5a,#a88a4a 40%,#7aa03a 70%,#5a8a2a)" role="img" aria-label="Photo of a park with white fences and benches"></div>
<div class="abs g-tile" style="left:453px;top:2219px;background:linear-gradient(180deg,#2e4a2a,#4a7a3a 50%,#7ab83a)" role="img" aria-label="Photo of a stone path leading to a waterfall"></div>
<div class="abs g-tile" style="left:764px;top:2219px;background:linear-gradient(180deg,#2a2a28,#1a1a18)" role="img" aria-label="Dark garden photo"></div>
<div class="abs g-tile g-brand brand-name" style="left:764px;top:2219px">Brimsett Gardening</div>
<a class="abs btn-brown" style="left:525px;top:2560px;width:150px;height:37px">VIEW ALL GALLERY</a>

<!-- testimonials -->
<section class="abs testimonials"></section>
<h2 class="abs section-title" style="top:2762px">Client <span>Testimonials</span></h2>

<div class="abs arrow" style="left:64px;top:2971px;border:2px solid var(--brown)">
  <svg width="14" height="22" viewBox="0 0 14 22"><path d="M11 2L3 11l8 9" fill="none" stroke="#a36f22" stroke-width="2.4"/></svg></div>
<div class="abs arrow" style="left:1080px;top:2971px;background:var(--brown)">
  <svg width="14" height="22" viewBox="0 0 14 22"><path d="M3 2l8 9-8 9" fill="none" stroke="#fff" stroke-width="2.4"/></svg></div>

<div class="abs t-card" style="left:141px">
  <div class="stars"><svg width="96" height="14" viewBox="0 0 96 14"><g fill="#e9a81c"><path id="st" d="M7 0l2 4.6 5 .4-3.8 3.3 1.2 4.9L7 10.6 2.6 13.2l1.2-4.9L0 5l5-.4z"/><use href="#st" x="20"/><use href="#st" x="40"/><use href="#st" x="60"/><use href="#st" x="80"/></g></svg></div>
  <div class="g-dot"></div>
  <p>Lorem ipsum dolor sit amet, consecte-tur adipiscing elit, sed do eiusmod tempor incididunt ut labore et dolore magna aliqua. Quis ipsum sus-pendisse ultrices gravida. Risus com-modo viverra maecenas accumsan lacus vel facilisis.</p>
  <h5>Elias Norren</h5>
</div>
<div class="abs t-card" style="left:453px">
  <div class="stars"><svg width="96" height="14" viewBox="0 0 96 14"><g fill="#e9a81c"><use href="#st"/><use href="#st" x="20"/><use href="#st" x="40"/><use href="#st" x="60"/><use href="#st" x="80"/></g></svg></div>
  <div class="g-dot"></div>
  <p>Lorem ipsum dolor sit amet, consecte-tur adipiscing elit, sed do eiusmod tempor incididunt ut labore et dolore magna aliqua. Quis ipsum sus-pendisse ultrices gravida. Risus com-modo viverra maecenas accumsan lacus vel facilisis.</p>
  <h5>Elias Norren</h5>
</div>
<div class="abs t-card" style="left:765px">
  <div class="stars"><svg width="96" height="14" viewBox="0 0 96 14"><g fill="#e9a81c"><use href="#st"/><use href="#st" x="20"/><use href="#st" x="40"/><use href="#st" x="60"/><use href="#st" x="80"/></g></svg></div>
  <div class="g-dot"></div>
  <p>Lorem ipsum dolor sit amet, consecte-tur adipiscing elit, sed do eiusmod tempor incididunt ut labore et dolore magna aliqua. Quis ipsum sus-pendisse ultrices gravida. Risus com-modo viverra maecenas accumsan lacus vel facilisis.</p>
  <h5>Elias Norren</h5>
</div>

<!-- contact -->
<section class="abs contact"></section>
<div class="abs contact-panel" role="img" aria-label="Dark garden photo behind contact details"></div>
<div class="abs cp-kicker">CONTACT US</div>
<h3 class="abs cp-title">Ask One Of Our<br>Experts For Help</h3>
<div class="abs cp-item" style="top:3491px;align-items:center">
  <span class="cp-icon"><svg width="13" height="13" viewBox="0 0 24 24"><path d="M5 3h4l2 5-2.5 1.5a11 11 0 0 0 6 6L16 13l5 2v4a2 2 0 0 1-2 2A17 17 0 0 1 3 5a2 2 0 0 1 2-2z" fill="none" stroke="#fff" stroke-width="2"/></svg></span>+91 123-456-7890</div>
<div class="abs cp-item" style="top:3543px;align-items:center">
  <span class="cp-icon" style="background:#fff"><svg width="13" height="10" viewBox="0 0 13 10"><rect x=".5" y=".5" width="12" height="9" fill="none" stroke="#111"/><path d="M.5.5l6 5 6-5" fill="none" stroke="#111"/></svg></span>hello@brimsettgardening.com</div>
<div class="abs cp-item" style="top:3588px">
  <span class="cp-icon"><svg width="11" height="14" viewBox="0 0 11 14"><path d="M5.5 13S1 8 1 5.2a4.5 4.5 0 0 1 9 0C10 8 5.5 13 5.5 13z" fill="none" stroke="#fff" stroke-width="1.5"/><circle cx="5.5" cy="5.2" r="1.5" fill="#fff"/></svg></span>
  <span>Lorem Ipsum is simply of the<br>printing and typesetting industry.</span></div>

<div class="abs form-title">DROP YOUR MESSAGE</div>
<div class="abs cfield active" style="left:515px;top:3395px;width:248px">First Name</div>
<div class="abs cfield" style="left:772px;top:3395px;width:248px">Last Name</div>
<div class="abs cfield" style="left:515px;top:3443px;width:248px">Email Address</div>
<div class="abs cfield" style="left:772px;top:3443px;width:248px">Phone</div>
<div class="abs cfield" style="left:515px;top:3493px;width:505px;height:137px">Message</div>
<a class="abs btn-brown" style="left:515px;top:3659px;width:128px;height:37px">SUBMIT NOW</a>

<!-- footer -->
<footer class="abs footer" role="img" aria-label="Dark garden photo behind the footer"></footer>
<div class="abs f-brand brand-name">Brimsett Gardening</div>
<a class="abs f-link" style="left:378px">Home</a>
<a class="abs f-link" style="left:450px">About Us</a>
<a class="abs f-link" style="left:543px">Services</a>
<a class="abs f-link" style="left:632px">Our Gallery</a>
<a class="abs f-link" style="left:742px">Contact Us</a>
<div class="abs f-rule" style="top:4118px"></div>
<div class="abs f-info" style="left:143px">
  <svg width="20" height="20" viewBox="0 0 20 20"><circle cx="10" cy="10" r="8.5" fill="none" stroke="#fff" stroke-width="1.3"/><path d="M1.5 10h17M10 1.5c3 3 3 14 0 17M10 1.5c-3 3-3 14 0 17" fill="none" stroke="#fff" stroke-width="1.1"/></svg>
  <span>Lorem Ipsum is simply dummy text<br>of the printing and typesetting.</span></div>
<div class="abs f-info" style="left:506px">
  <svg width="20" height="20" viewBox="0 0 24 24"><path d="M5 3h4l2 5-2.5 1.5a11 11 0 0 0 6 6L16 13l5 2v4a2 2 0 0 1-2 2A17 17 0 0 1 3 5a2 2 0 0 1 2-2z" fill="none" stroke="#fff" stroke-width="1.5"/></svg>
  <span>Call Us<br>123-456-7890</span></div>
<div class="abs f-info" style="left:798px">
  <svg width="22" height="18" viewBox="0 0 22 18"><path d="M1 7l10-6 10 6v10H1z M1 7l10 6 10-6" fill="none" stroke="#fff" stroke-width="1.3"/></svg>
  <span>Email<br>hello@brimsettgardening.com</span></div>
<div class="abs f-rule" style="top:4202px"></div>
<div class="abs copyright">© 2024 Brimsett Gardening. All Rights Reserved.</div>

</body>
</html>
```